New Company Letterhead

Hi All

We are looking for a fresh new letterhead. At present we have rolling colour behind our logo but would like one flat colour. See attached for examples of our current letterhead, logos and company colour chart. All information currently contained within the letterhead (i.e. address, ABN, tel, fax, email etc) needs to still be included in the new letterhead. Preferred font is Helvetica or something similar.

Any queries please shout.

Many thanks & best of luck,

Rosalind Pembury
Barwick Estate Agents

Hi Designers Great work so far! Would it be possible to add to your designs the phrase; Done. Different. Preferably in a light grey? Many thanks, Ros

```html
<!DOCTYPE html>
<html lang="en">
<head>
<meta charset="utf-8">
<title>Barwick Estate Agents – Letterhead</title>
<link href="https://fonts.googleapis.com/css2?family=Arimo:wght@400;700&display=swap" rel="stylesheet">
<style>
  :root {
    --brand-navy: #0f4a66;
    --footer-grey: #9a9a9a;
    --label-grey: #7a7a7a;
    --edge-bar: #a9a9a9;
    --paper: #ffffff;
    --backdrop: #e8e9eb;
  }
  * { margin: 0; padding: 0; box-sizing: border-box; }
  html, body {
    width: 1200px;
    height: 1200px;
    overflow: hidden;
    background: var(--backdrop);
    font-family: "Arimo", Arial, Helvetica, sans-serif;
  }
  .letterhead {
    position: absolute;
    left: 160px;
    top: 30px;
    width: 881px;
    height: 1140px;
    background: var(--paper);
  }
  .brand-name {
    position: absolute;
    top: 102px;
    left: 0;
    width: 100%;
    text-align: center;
    color: var(--brand-navy);
    font-size: 31px;
    font-weight: 400;
    line-height: 36px;
  }
  .edge-bar {
    position: absolute;
    top: 1011px;
    width: 20px;
    height: 86px;
    background: var(--edge-bar);
  }
  .edge-bar--left { left: 0; }
  .edge-bar--right { right: 0; }
  .footer {
    position: absolute;
    top: 1014px;
    left: 0;
    width: 100%;
    text-align: center;
    color: var(--footer-grey);
    font-size: 12.5px;
    line-height: 1.45;
  }
  .footer-company { font-weight: 700; }
  .footer-address { margin-top: 7px; }
  .footer-contacts { margin-top: 3px; white-space: nowrap; }
  .footer-contacts .label { font-weight: 700; color: var(--label-grey); }
  .footer-contacts .divider { margin: 0 12px; }
</style>
</head>
<body>
  <main class="letterhead">
    <h1 class="brand-name">Barwick Estate Agents</h1>

    <div class="edge-bar edge-bar--left"></div>
    <div class="edge-bar edge-bar--right"></div>

    <footer class="footer">
      <p class="footer-company">Barwick Estate Agents</p>
      <p class="footer-abn">ABN: 47 508 913 206</p>
      <p class="footer-address">12 Harbour Street, Wren Point NSW 2264</p>
      <p class="footer-contacts">
        <span class="label">P</span> (02) 5550 1420<span class="divider">| |</span><span class="label">F</span> (02) 5550 1421<span class="divider">| |</span><span class="label">E</span> management@barwickestateagents.com.au<span class="divider">| |</span><span class="label">W</span> www.barwickestateagents.com.au
      </p>
    </footer>
  </main>
</body>
</html>
```